Aunt Roula's Bakery

I am about to create a luxury boutique that specializes in cake baking and cupcake
and ready for parties and special events and order delivery
the logo has already made

Boutique

Email:auntroulasbakery@mailbox-example.net
Instagram: aunt_roula_bakery
Twitter: xxxxxxx
WhatsApp: xxxxxxx

Requirements
Must have
• luxury design

```html
<!DOCTYPE html>
<html lang="en">
<head>
<meta charset="utf-8">
<title>Aunt Roula's Bakery – Business Card</title>
<link rel="stylesheet" href="https://fonts.googleapis.com/css2?family=Open+Sans:wght@400;600&display=swap">
<style>
  :root {
    --bg: #efe9e2;
    --card-black: #0c0c0c;
    --card-black-soft: #1d1d1d;
    --blush: #df9aaa;
    --stone: #8a8a86;
    --logo-grey: #b9b9b9;
    --white: #ffffff;
    --contact-text: #f2f2f2;
  }
  html, body {
    margin: 0;
    padding: 0;
    width: 1200px;
    height: 900px;
    overflow: hidden;
    background: var(--bg);
    font-family: "Open Sans", sans-serif;
  }
  .canvas {
    position: relative;
    width: 1200px;
    height: 900px;
  }
  .card {
    position: absolute;
    width: 700px;
    height: 400px;
    overflow: hidden;
    background: radial-gradient(ellipse at 45% 35%, var(--card-black-soft), var(--card-black) 70%);
    box-shadow: 0 10px 30px rgba(0,0,0,0.25);
  }
  .card--front { left: 80px; top: 60px; }
  .card--back { left: 420px; top: 440px; }

  .brand {
    position: absolute;
    display: flex;
    align-items: center;
    gap: 14px;
    font-weight: 600;
    text-transform: uppercase;
    letter-spacing: 0.08em;
    white-space: nowrap;
  }
  .brand__dot {
    border-radius: 50%;
    flex: none;
  }
  .card--front .brand {
    left: 50%;
    top: 50%;
    transform: translate(-50%, -50%);
    color: var(--white);
    font-size: 34px;
  }
  .card--front .brand__dot {
    width: 48px; height: 48px;
    background: var(--white);
  }
  .card--back .brand {
    right: 40px;
    top: 60px;
    color: var(--logo-grey);
    font-size: 24px;
  }
  .card--back .brand__dot {
    width: 38px; height: 38px;
    background: var(--blush);
  }

  .card__wave {
    position: absolute;
    left: 0; top: 0;
    width: 700px; height: 400px;
  }
  .contact-list {
    position: absolute;
    left: 140px;
    top: 165px;
    margin: 0;
    padding: 0;
    list-style: none;
    color: var(--contact-text);
    font-size: 15px;
    line-height: 26px;
  }
  .contact-list__item {
    display: flex;
    align-items: center;
    gap: 10px;
  }
  .contact-list__icon {
    width: 12px; height: 12px;
    flex: none;
  }
  .contact-list__mark {
    width: 11px; height: 11px;
    background: var(--blush);
    border-radius: 2px;
    flex: none;
  }
</style>
</head>
<body>
<main class="canvas">

  <section class="card card--front" aria-label="Card front">
    <div class="brand">
      <span class="brand__dot"></span>
      <span class="brand__name">Aunt Roula's Bakery</span>
    </div>
  </section>

  <section class="card card--back" aria-label="Card back">
    <svg class="card__wave" viewBox="0 0 700 400" aria-hidden="true">
      <path d="M0 330 C 150 330, 330 300, 470 230 C 560 185, 640 160, 700 160 L700 400 L0 400 Z" fill="var(--stone)"/>
      <path d="M0 355 C 160 350, 340 320, 480 250 C 570 205, 645 180, 700 178 L700 400 L0 400 Z" fill="var(--card-black)"/>
      <path d="M0 372 C 170 365, 360 330, 500 262 C 590 218, 650 180, 700 170 L700 400 L0 400 Z" fill="var(--blush)"/>
    </svg>

    <div class="brand">
      <span class="brand__dot"></span>
      <span class="brand__name">Aunt Roula's Bakery</span>
    </div>

    <ul class="contact-list">
      <li class="contact-list__item">
        <svg class="contact-list__icon" viewBox="0 0 12 12" aria-hidden="true">
          <rect x="0" y="2" width="12" height="8" fill="var(--blush)"/>
          <path d="M0 2 L6 7 L12 2" fill="none" stroke="var(--card-black)" stroke-width="1"/>
        </svg>
        <span>auntroulasbakery@mailbox-example.net</span>
      </li>
      <li class="contact-list__item">
        <span class="contact-list__mark"></span>
        <span>aunt_roula_bakery</span>
      </li>
      <li class="contact-list__item">
        <span class="contact-list__mark"></span>
        <span>xxxxxxx</span>
      </li>
      <li class="contact-list__item">
        <span class="contact-list__mark"></span>
        <span>xxxxxxx</span>
      </li>
    </ul>
  </section>

</main>
</body>
</html>
```